Gestaltung Mini Katalog für bayerische Polomarke
Gestaltung "Mini" Katalog für bayerische Polomarke
Zielgruppe
Unsere Marke richtet sich an den klassischen Lifestyle Kunden. 20 - 45 Jahre alt, legt Wert auf das Äussere und Kleidung.... Mag es gerne besonders, modern und chic.
Hallo,
wir planen derzeit einen kleinen Katalog von 8-10 Seiten im Format DIN A5 (kein Muss). Präsentiert wird darin die erste bayerische Polomarke K&M reitmode und die aktuellen Kollektionen an Polo-Teamshirts.
Die Fotos dazu werden in den nächsten 14 Tagen entstehen.
Wir suchen nun jemanden, der uns das ganze in eine moderne Gestaltung bringt. Für Vorschläge bitte statt der Fotos alternative Fotos einsetzen.
Unsere Marke bewegt sich im mittleren Preissegment und präsentiert eine ganz besondere Sportart. All das muss in dem Katalog rüber kommen. Neben den Produkt- und Modefotos werden klassische Polobilder integriert, um das Gefühl diesen Sports mit zu vermitteln.
Die Grundfarben sollten sich an denen von K&M reitmode orientieren: schwarz, blau, weiss.... Wobei wir für andere Farben, wenn diese passen bzw. begründet sind auch interessiert sind.

```html
<!DOCTYPE html>
<html lang="de">
<head>
<meta charset="utf-8">
<title>K&amp;M reitmode – Herren-Kollektionen</title>
<link href="https://fonts.googleapis.com/css2?family=Roboto+Condensed:wght@300;400;700&display=swap" rel="stylesheet">
<style>
  :root{
    --paper:#ffffff;
    --ink:#333333;
    --muted:#888888;
    --accent:#1a9bd7;
    --headline-grey:#e4e4e4;
    --shirt-dark:#141414;
    --shirt-mid:#2c2c2c;
    --shirt-slate:#4b5a6b;
    --shirt-slate-light:#5f6e80;
    --photo-sky:#1f3f6b;
    --photo-warm:#c98a6a;
    --photo-red:#b8322e;
  }
  *{box-sizing:border-box;margin:0;padding:0}
  html,body{width:1200px;height:423px;overflow:hidden;background:var(--paper)}
  body{font-family:"Roboto Condensed",Arial,sans-serif;color:var(--ink);position:relative}
  .spread{position:absolute;inset:0;width:1200px;height:423px;overflow:hidden}

  .folio{position:absolute;top:7px;font-size:8px;color:var(--muted);letter-spacing:.2px;z-index:2}
  .folio b{color:var(--accent);font-weight:400}
  .folio--left{left:10px}
  .folio--right{right:8px;color:#f0f0f0}
  .folio--right b{color:#f0f0f0}

  .product-shot{position:absolute;border-radius:38% 38% 30% 30%;
    background:radial-gradient(ellipse at 50% 40%,var(--shirt-mid),var(--shirt-dark) 80%)}
  .product-shot--slate{background:radial-gradient(ellipse at 50% 40%,var(--shirt-slate-light),var(--shirt-slate) 80%)}

  .product{position:absolute;width:170px}
  .product__title{color:var(--accent);font-size:9px;font-weight:700;margin-bottom:7px}
  .product__text{font-size:6.8px;line-height:1.5;color:var(--ink)}
  .product__text p+p{margin-top:7px}
  .product__meta{position:absolute;display:flex;gap:24px;font-size:6.8px;color:var(--ink)}
  .price{line-height:1}
  .price strong{color:var(--accent);font-size:9px;font-weight:700}
  .price small{display:block;font-size:4.5px;color:var(--muted);margin-left:22px;margin-top:1px}

  .tile-label{position:absolute;color:var(--accent);font-size:7.5px;font-weight:700}
  .tile-meta{position:absolute;display:flex;gap:22px;font-size:6.3px}

  .right-note{position:absolute;left:637px;top:391px;width:310px;font-size:6.5px;line-height:1.5}

  .page-headline{position:absolute;left:3px;bottom:-3px;font-size:26px;font-weight:700;
    color:var(--headline-grey);letter-spacing:.5px}

  .mood-photo{position:absolute;left:960px;top:0;width:240px;height:423px;
    background:linear-gradient(160deg,var(--photo-sky) 0%,#2c4f7c 30%,var(--photo-warm) 55%,#e8d8c8 70%,var(--photo-red) 90%)}
</style>
</head>
<body>
<main class="spread">
  <div class="folio folio--left">4 | <b>www.km-reitmode.de</b></div>

  <div class="product-shot" style="left:26px;top:46px;width:146px;height:106px" role="img" aria-label="Produktfoto: schwarzes Langarm-Teamshirt mit Rückennummer 3"></div>
  <div class="product-shot" style="left:212px;top:46px;width:124px;height:104px" role="img" aria-label="Produktfoto: schwarzes Team Shirt 2008, Vorderseite"></div>
  <div class="product-shot" style="left:308px;top:160px;width:66px;height:50px" role="img" aria-label="Produktfoto: Team Shirt 2008, Rückseite mit Nummer 3"></div>
  <div class="product-shot" style="left:410px;top:46px;width:106px;height:106px" role="img" aria-label="Produktfoto: schwarzes Poloshirt mit Brustmotiv"></div>

  <section class="product" style="left:22px;top:256px">
    <h2 class="product__title">Original Team Langarm-Shirt 2008 Herren</h2>
    <div class="product__text">
      <p>In diesem Shirt spielte der Isartal Polo Club in der Saison 2008. Poloshirt schwarz, fein bestickt, hochwertig aus gekämmter Baumwolle. Das Teamshirt des Isartal Polo Club gibt es nun auch mit exklusivem K&amp;M Stick.</p>
      <p>Erhältlich in den Größen S, M, L, XL und XXL.</p>
    </div>
  </section>
  <div class="product__meta" style="left:22px;top:340px">
    <span class="price">Preis: <strong>65.00 EUR</strong><small>Preis inkl. MwSt.</small></span>
    <span>Bestell-Nr.: 080803</span>
  </div>

  <section class="product" style="left:214px;top:256px">
    <h2 class="product__title">Original Team Shirt 2008</h2>
    <div class="product__text">
      <p>In diesem Shirt spielte der Isartal Polo Club in der Saison 2008. Poloshirt schwarz, fein bestickt, hochwertig aus gekämmter Baumwolle.</p>
      <p>Erhältlich in den Größen S, M, L, XL und XXL.</p>
    </div>
  </section>
  <div class="product__meta" style="left:214px;top:340px">
    <span class="price">Preis: <strong>49.00 EUR</strong><small>Preis inkl. MwSt.</small></span>
    <span>Bestell-Nr.: 080801</span>
  </div>

  <section class="product" style="left:406px;top:256px">
    <h2 class="product__title">Poloshirt</h2>
    <div class="product__text">
      <p>Das K&amp;M Polo für den Alltag in schwarz, mit kleinem gesticktem Motiv auf der Brust. Poloshirt der Marke Verano aus 100% ringgesponnener gekämmter Baumwolle, Zweiknopfleiste, Nackenband und verstärkter Schulternaht.</p>
      <p>Erhältlich in den Größen S, M, L, XL und XXL.</p>
    </div>
  </section>
  <div class="product__meta" style="left:406px;top:340px">
    <span class="price">Preis: <strong>49.95 EUR</strong><small>Preis inkl. MwSt.</small></span>
    <span>Bestell-Nr.: 080802</span>
  </div>

  <div class="page-headline">HERREN-Kollektionen</div>

  <div class="product-shot" style="left:666px;top:14px;width:94px;height:124px" role="img" aria-label="Produktfoto: schwarzes T-Shirt mit weißem Polospieler-Druck"></div>
  <div class="product-shot" style="left:850px;top:14px;width:94px;height:124px" role="img" aria-label="Produktfoto: schwarzes T-Shirt mit Spielerdruck und blauer Zahl 2"></div>
  <div class="product-shot" style="left:666px;top:204px;width:94px;height:128px" role="img" aria-label="Produktfoto: schwarzes T-Shirt mit blauem Polopferd-Druck"></div>
  <div class="product-shot product-shot--slate" style="left:850px;top:204px;width:94px;height:128px" role="img" aria-label="Produktfoto: graublaues T-Shirt mit blauem Polopferd-Druck"></div>

  <div class="tile-label" style="left:637px;top:152px">Shirt POLO</div>
  <div class="tile-meta" style="left:637px;top:170px"><span>Bestell-Nr.: 080101</span><span class="price">Preis: <strong>25.00 EUR</strong><small>Preis inkl. MwSt.</small></span></div>
  <div class="tile-label" style="left:815px;top:152px">Shirt TOP POLO</div>
  <div class="tile-meta" style="left:815px;top:170px"><span>Bestell-Nr.: 080101</span><span class="price">Preis: <strong>25.00 EUR</strong><small>Preis inkl. MwSt.</small></span></div>
  <div class="tile-label" style="left:637px;top:340px">Shirt POLO B</div>
  <div class="tile-meta" style="left:637px;top:358px"><span>Bestell-Nr.: 080101</span><span class="price">Preis: <strong>25.00 EUR</strong><small>Preis inkl. MwSt.</small></span></div>
  <div class="tile-label" style="left:815px;top:340px">Shirt POLO C</div>
  <div class="tile-meta" style="left:815px;top:358px"><span>Bestell-Nr.: 080101</span><span class="price">Preis: <strong>25.00 EUR</strong><small>Preis inkl. MwSt.</small></span></div>

  <p class="right-note">Die Shirt von <strong>K&amp;M reitmode</strong> je nach Ausführung mit gedrucktem oder gesticktem Motiv. Taillierte Herren-Shirts, enganliegend, aus 100% gekämmter Baumwolle, fallen eher klein aus.</p>

  <div class="mood-photo" role="img" aria-label="Stimmungsfoto: Polospieler mit Helm und Schläger vor blauem Himmel"></div>
  <div class="folio folio--right"><b>www.km-reitmode.de</b> | 5</div>
</main>
</body>
</html>
```